Infografik/ Zeitleiste für Startup
Zielgruppe
Wir sind ein Startup, das über die Seite Kalendaro.de zukünftig folgenden Service anbietet: Unternehmer können sehr flexibel (selbst) gestaltete Terminformulare erstellen und auf Ihrer Website einbinden. Kunden können dann diese Termine buchen und bekommen dann Erinnerungs-Mails und SMS.
Zielgruppe: Dienstleister wie Fotografen, Friseure, Versicherungsvertreter, Masseure, Restaurants, Arztpraxen. Also alle, die darauf angewiesen sind, dass vereinbarte Termine eingehalten werden und die die Terminvereinbarung vereinfachen wollen. Also weniger per Telefon, mehr über die eigene Website.
Kalendaro ist mit PunktWahl.com (aktuell noch Top-und-Flop.com) verknüpft. Kunden, die einen Termin wünschen, sehen die Bewertungen vorheriger Kunden. Das stärkt das Vertrauen und erhöht die Termin-Zuverlässigkeit (Verbessert die No-Show-Rate). Damit sinken auch die Werbekosten je Kunden (geringere Kosten pro Conversion).
Kalendaro.de und PunktWahl.com (aktuell noch Top-und-Flop.com) wurde vom Team von Bilder-Atelier.de entwickelt. Dank Kalendaro und PunktWahl.com haben wir (das Team von Bilder-Atelier.de) folgende Vorteile:
- verbesserte Termin-Zuverlässigkeit (No-Show-Rate)
- mehr Kunden, mehr Shootings
- höherer Umsatz
- Zeitersparnis bei der Terminvereinbarung
- Senkungen der Werbekosten je Kunden (geringere Kosten pro Conversion)
Das ist der Grund, warum wir Kalendaro und PunktWahl nun auch für andere Branchen anbieten.
Siehe auch: https://www.videoplattform.example/watch?v=Qm7Rt2Lp9Xz
Siehe auch: https://www.videoplattform.example/watch?v=Vn4Kd8Sw3Hb
Aufgabenstellung
Wir benötigen für Kalendaro.de eine Infografik. Diese soll verdeutlichen, welche Vorteile wir (Bilder-Atelier.de) dank Kalendaro und PunktWahl haben:
Der Betrachter soll diese Zahlen auf einen Blick werten und die Vorteile für SEIN GESCHÄFT erkennen können. Zum Beispiel anhand einer Zeitleiste, die die Entwicklung der verschiedenen Kennzahlen wiedergibt.
Die Kennzahlen (die Entwicklung) können Sie hier aufrufen: https://ablage.example/ordner/7KpRwZ2mNc5Qx8LtVb3HyJ6dFs9GaE1Uo?usp=sharing
Besonders soll die positive Entwicklung ab Ende September 2017 deutlich werden. Ab Ende September 2017 haben wir Kalendaro und PunktWahl.com für die Terminvereinbarung genutzt. Vorher haben wir Termine per Email und Telefon vereinbart, was deutlich zeitintensiver war.
Das Design der Zeitleiste (der Infografik) soll sich an Kalendaro.de orientieren.
Falls die sechs Kennzahlen nicht übersichtlich in einer Zeitleiste darstellbar sind, könnten die Kennzahlen auf mehrere Grafiken aufgeteilt werden.
Vorstellbar ist auch eine interaktive Infografik, bei der man die jeweilige Kennzahl auswählen kann.
Wir lassen uns hier gerne von Ihrer Kreativität überraschen. Der spätere Kunde/Nutzer/ Betrachter der Infografik steht bitte im Vordergrund jeder Überlegung/jedes Designs.
Nutzen Sie ggf. bitte Icons und verschiedenen Farben, um die verschiedenen Kennzahlen auch visuell zu verdeutlichen.
Die Infografik soll später auf https://developer.kalendaro.de/de/about-us.html und in Flyern veröffentlicht werden.
Wesentliche Funktionen und Vorteile siehe auch:
https://www.videoplattform.example/watch?v=Qm7Rt2Lp9Xz
https://www.videoplattform.example/watch?v=Vn4Kd8Sw3Hb
Die einzelnen gr..

```html
<!DOCTYPE html>
<html lang="de">
<head>
<meta charset="utf-8">
<title>Shootings – Zeitleiste</title>
<link rel="stylesheet" href="https://fonts.googleapis.com/css2?family=Barlow:wght@400;500;600;700&display=swap">
<style>
  :root {
    --red: #e30613;
    --grey-text: #6e6f71;
    --label-text: #5d5f62;
    --bar-before: #a3a7ab;
    --bar-after: #747b83;
    --label-row: #f3f3f4;
    --tick: #c9ccd0;
    --green: #7cb928;
    --yellow: #f5c200;
    --white: #ffffff;
  }
  html, body {
    margin: 0;
    padding: 0;
    width: 1200px;
    height: 483px;
    overflow: hidden;
    background: var(--white);
  }
  .infographic {
    display: block;
    width: 1200px;
    height: 483px;
    font-family: "Barlow", sans-serif;
  }
  .nav-link { font-size: 12.5px; font-weight: 500; fill: var(--grey-text); }
  .section-title { font-size: 16px; font-weight: 700; fill: var(--white); letter-spacing: 0.6px; }
  .value { font-size: 11.5px; font-weight: 500; fill: var(--grey-text); text-anchor: middle; }
  .month { font-size: 8px; font-weight: 500; fill: var(--label-text); text-anchor: middle; }
  .phase-label { font-size: 14px; font-weight: 700; fill: var(--white); text-anchor: middle; letter-spacing: 1.2px; }
  .tick { stroke: var(--tick); stroke-width: 0.8; }
  .shutter { fill: var(--red); }
  .blade { fill: none; stroke: var(--white); stroke-width: 0.09; stroke-linecap: round; }
  .icon-glyph { fill: none; stroke: var(--white); stroke-width: 1.4; stroke-linecap: round; stroke-linejoin: round; }
</style>
</head>
<body>
<svg class="infographic" viewBox="0 0 1200 483" xmlns="http://www.w3.org/2000/svg" role="img" aria-label="Zeitleiste Shootings pro Monat von Mai 2017 bis September 2018">
  <defs>
    <linearGradient id="bg-before" x1="0" x2="1" y1="0" y2="0">
      <stop offset="0" stop-color="#c3c8ce"/>
      <stop offset="0.55" stop-color="#e3e6e9"/>
      <stop offset="1" stop-color="#fafafb"/>
    </linearGradient>
    <linearGradient id="bg-after" x1="0" x2="1" y1="0" y2="0">
      <stop offset="0" stop-color="#e2e5e8"/>
      <stop offset="1" stop-color="#f8f9fa"/>
    </linearGradient>
    <symbol id="shutter" viewBox="-1 -1 2 2" overflow="visible">
      <circle class="shutter" r="1"/>
      <g class="blade">
        <path d="M0.32 -0.18 Q0.2 -0.7 -0.35 -0.94"/>
        <path d="M0.32 -0.18 Q0.2 -0.7 -0.35 -0.94" transform="rotate(60)"/>
        <path d="M0.32 -0.18 Q0.2 -0.7 -0.35 -0.94" transform="rotate(120)"/>
        <path d="M0.32 -0.18 Q0.2 -0.7 -0.35 -0.94" transform="rotate(180)"/>
        <path d="M0.32 -0.18 Q0.2 -0.7 -0.35 -0.94" transform="rotate(240)"/>
        <path d="M0.32 -0.18 Q0.2 -0.7 -0.35 -0.94" transform="rotate(300)"/>
      </g>
    </symbol>
  </defs>

  <!-- navigation -->
  <g class="nav">
    <text class="nav-link" x="910" y="91">zurück zu Übersicht</text>
    <path d="M959 89 L959 112 L964 107 L968 115 L971 113.5 L967 106 L974 106 Z" fill="#000" stroke="#fff" stroke-width="1"/>
    <g class="metric-icons">
      <circle cx="1039" cy="86" r="8" fill="var(--green)"/>
      <path class="icon-glyph" d="M1039 86 L1039 82 M1037 77 L1041 77"/>
      <circle cx="1063" cy="86" r="8" fill="var(--yellow)"/>
      <path class="icon-glyph" d="M1066 82.5 A4 4 0 1 0 1066 89.5 M1059.5 85 L1064 85 M1059.5 87.5 L1064 87.5"/>
      <circle cx="1088" cy="86" r="8" fill="var(--red)"/>
      <path class="icon-glyph" d="M1085 82 L1091 82 L1091 88 L1085 88 Z M1084 90.5 L1092 90.5"/>
      <circle cx="1112" cy="86" r="8" fill="var(--green)"/>
      <path class="icon-glyph" d="M1108 87 Q1112 91.5 1116 87"/>
      <circle cx="1135" cy="86" r="8" fill="var(--yellow)"/>
      <path class="icon-glyph" d="M1131 84.5 L1131 87.5 L1135 87.5 L1139 90 L1139 82 L1135 84.5 Z"/>
    </g>
  </g>

  <!-- chart frame -->
  <rect x="74" y="127" width="337" height="112" fill="url(#bg-before)"/>
  <rect x="411" y="127" width="729" height="112" fill="url(#bg-after)"/>
  <rect x="74" y="239" width="1066" height="30" fill="var(--label-row)"/>
  <rect x="74" y="120" width="1066" height="7" fill="var(--red)"/>
  <path d="M74 120 H234 V147 Q234 153 228 153 H74 Z" fill="var(--red)"/>
  <text class="section-title" x="82" y="143">SHOOTINGS</text>
  <rect x="411" y="127" width="8" height="26" fill="#c8cbce"/>

  <!-- ticks -->
  <g class="ticks">
    <line class="tick" x1="233" y1="127" x2="233" y2="153"/>
    <line class="tick" x1="294" y1="127" x2="294" y2="153"/>
    <line class="tick" x1="355" y1="127" x2="355" y2="153"/>
    <line class="tick" x1="477" y1="127" x2="477" y2="153"/>
    <line class="tick" x1="538" y1="127" x2="538" y2="153"/>
    <line class="tick" x1="599" y1="127" x2="599" y2="153"/>
    <line class="tick" x1="660" y1="127" x2="660" y2="153"/>
    <line class="tick" x1="721" y1="127" x2="721" y2="153"/>
    <line class="tick" x1="782" y1="127" x2="782" y2="153"/>
    <line class="tick" x1="843" y1="127" x2="843" y2="153"/>
    <line class="tick" x1="904" y1="127" x2="904" y2="153"/>
    <line class="tick" x1="965" y1="127" x2="965" y2="153"/>
    <line class="tick" x1="1026" y1="127" x2="1026" y2="153"/>
    <line class="tick" x1="1087" y1="127" x2="1087" y2="153"/>
  </g>

  <!-- data points: radius ≈ 1.3 × value -->
  <g class="data-points">
    <use href="#shutter" x="100.3" y="174.3" width="23.4" height="23.4"/>
    <use href="#shutter" x="161.6" y="175.6" width="20.8" height="20.8"/>
    <use href="#shutter" x="220" y="173" width="26" height="26"/>
    <use href="#shutter" x="282.3" y="174.3" width="23.4" height="23.4"/>
    <use href="#shutter" x="342" y="173" width="26" height="26"/>
    <use href="#shutter" x="398.4" y="170.4" width="31.2" height="31.2"/>
    <use href="#shutter" x="460.1" y="169.1" width="33.8" height="33.8"/>
    <use href="#shutter" x="526.3" y="174.3" width="23.4" height="23.4"/>
    <use href="#shutter" x="578.2" y="165.2" width="41.6" height="41.6"/>
    <use href="#shutter" x="635.3" y="161.3" width="49.4" height="49.4"/>
    <use href="#shutter" x="691.1" y="156.1" width="59.8" height="59.8"/>
    <use href="#shutter" x="754.7" y="158.7" width="54.6" height="54.6"/>
    <use href="#shutter" x="819.6" y="162.6" width="46.8" height="46.8"/>
    <use href="#shutter" x="878" y="160" width="52" height="52"/>
    <use href="#shutter" x="945.5" y="166.5" width="39" height="39"/>
    <use href="#shutter" x="1010.4" y="170.4" width="31.2" height="31.2"/>
    <use href="#shutter" x="1054.5" y="153.5" width="65" height="65"/>
  </g>

  <g class="values">
    <text class="value" x="112" y="229">9</text>
    <text class="value" x="172" y="232">8</text>
    <text class="value" x="233" y="232">10</text>
    <text class="value" x="294" y="232">9</text>
    <text class="value" x="355" y="232">10</text>
    <text class="value" x="414" y="232">12</text>
    <text class="value" x="476" y="232">13</text>
    <text class="value" x="538" y="232">9</text>
    <text class="value" x="599" y="232">16</text>
    <text class="value" x="661" y="232">19</text>
    <text class="value" x="721" y="232">23</text>
    <text class="value" x="781" y="232">21</text>
    <text class="value" x="844" y="232">18</text>
    <text class="value" x="904" y="232">20</text>
    <text class="value" x="965" y="232">15</text>
    <text class="value" x="1027" y="232">12</text>
    <text class="value" x="1087" y="232">25</text>
  </g>

  <g class="months">
    <text class="month" x="110" y="263">Mai 17</text>
    <text class="month" x="172" y="263">Juni 17</text>
    <text class="month" x="232" y="263">Juli 17</text>
    <text class="month" x="293" y="263">Aug 17</text>
    <text class="month" x="354" y="263">Sep 17</text>
    <text class="month" x="413" y="263">Okt 17</text>
    <text class="month" x="476" y="263">Nov17</text>
    <text class="month" x="537" y="263">Dez 17</text>
    <text class="month" x="598" y="263">Jan 18</text>
    <text class="month" x="659" y="263">Feb 18</text>
    <text class="month" x="720" y="263">Mär 18</text>
    <text class="month" x="781" y="263">Apr 18</text>
    <text class="month" x="841" y="263">Mai 18</text>
    <text class="month" x="902" y="263">Jun 18</text>
    <text class="month" x="963" y="263">Jul 18</text>
    <text class="month" x="1024" y="263">Aug 18</text>
    <text class="month" x="1085" y="263">Sep 18</text>
  </g>

  <!-- phases -->
  <rect x="73" y="269" width="336" height="24" fill="var(--bar-before)"/>
  <text class="phase-label" x="241" y="286">OHNE TERMIN-TOOL</text>
  <rect x="417" y="269" width="723" height="24" fill="var(--bar-after)"/>
  <text class="phase-label" x="778" y="286">NUTZUNG KALENDARO UND PUNKTWAHL</text>
</svg>
</body>
</html>
```